Construction company business card

One side to be the logo with the company name, The other side I would like: (Tomas verbick) Project manager 41 barrow crescent hallam 52917306224783(03) 9703 2428Info@gudeljgroup.comAnd then maybe a couple dot points saying what we do:Construction (commercial & industrial) Civil construction

Anything else please contact me!
Maybe curved st one edge of the card

Target Market(s)

Older clientele

Industry/Entity Type

Construction Company

Contact Information for Business Card

Read above

Colors
3277b5
1b1b1b
9d9d9d

Requirements
Must have
• Use my logo on one side
Nice to have
• Read above
Should not have
• Read above

```html
<!DOCTYPE html>
<html lang="en">
<head>
<meta charset="utf-8">
<title>Stonevale Property Group – Business Card</title>
<link rel="stylesheet" href="https://fonts.googleapis.com/css2?family=Roboto:wght@400;500;700;900&display=swap">
<style>
  :root {
    --blue: #3277b5;
    --blue-deep: #2d5f94;
    --ink: #1b1b1b;
    --grey: #9d9d9d;
    --card-top: #f4f4f4;
    --card-bottom: #e6e6e6;
    --backdrop: #b9b9b9;
  }
  * { margin: 0; padding: 0; box-sizing: border-box; }
  html, body {
    width: 1200px; height: 576px; overflow: hidden;
    background: var(--backdrop);
    font-family: "Roboto", Arial, sans-serif;
    color: var(--ink);
  }
  .canvas { position: relative; width: 1200px; height: 576px; }

  .card {
    position: absolute; top: 138px;
    width: 484px; height: 294px;
    background: linear-gradient(170deg, var(--card-top), var(--card-bottom));
    border-top-right-radius: 26px;
    border-bottom-left-radius: 8px;
    overflow: hidden;
    box-shadow: 0 3px 6px rgba(0,0,0,.18);
  }
  .card--front { left: 82px; }
  .card--back { left: 602px; }

  .card__band { position: absolute; left: 0; right: 0; bottom: 0; height: 13px; display: flex; }
  .card__band-grey { flex: 1; background: var(--grey); }
  .card__band-blue { flex: 1; background: var(--blue-deep); }

  .brand-dot { position: absolute; border-radius: 50%; background: var(--blue-deep); }
  .brand-name {
    position: absolute; font-weight: 900; color: var(--blue-deep);
    text-transform: uppercase; line-height: 1.05;
  }

  /* Front */
  .card--front .brand-dot { width: 84px; height: 84px; left: 200px; top: 40px; }
  .card--front .brand-name { left: 0; right: 0; top: 148px; text-align: center; font-size: 30px; letter-spacing: 1px; }
  .card--front .brand-name span { display: block; font-size: 15px; letter-spacing: 4.5px; }
  .front__web {
    position: absolute; left: 0; right: 0; top: 234px;
    display: flex; justify-content: center; align-items: center; gap: 10px;
    font-size: 12.5px;
  }
  .front__web::before, .front__web::after {
    content: ""; width: 34px; height: 2px; background: var(--grey); border-radius: 2px;
  }
  .tagline { position: absolute; left: 0; right: 0; text-align: center; font-size: 13px; }
  .card--front .tagline { top: 255px; }

  /* Back */
  .card--back .brand-dot { width: 64px; height: 64px; left: 86px; top: 38px; }
  .card--back .brand-name { left: 168px; top: 48px; font-size: 27px; letter-spacing: .5px; }
  .card--back .brand-name span { display: block; font-size: 13px; letter-spacing: 3.6px; }

  .person { position: absolute; right: 248px; top: 150px; text-align: right; font-size: 12.5px; }
  .person__name { font-size: 17px; font-weight: 700; color: var(--blue-deep); margin-bottom: 5px; }
  .person__role { margin-bottom: 9px; }

  .contacts { position: absolute; left: 258px; top: 153px; list-style: none; font-size: 12.5px; }
  .contacts li { display: flex; align-items: center; gap: 10px; height: 19px; }
  .contacts svg { width: 11px; height: 11px; fill: var(--blue-deep); }
  .card--back .tagline { top: 247px; color: var(--blue-deep); font-size: 12px; }
</style>
</head>
<body>
<div class="canvas">

  <section class="card card--front">
    <div class="brand-dot"></div>
    <div class="brand-name">Stonevale<span>Property Group</span></div>
    <p class="front__web">www.stonevaleproperty.com</p>
    <p class="tagline">Construction (Commercial &amp; Industrial) Civil Construction</p>
    <div class="card__band"><div class="card__band-grey"></div><div class="card__band-blue"></div></div>
  </section>

  <section class="card card--back">
    <div class="brand-dot"></div>
    <div class="brand-name">Stonevale<span>Property Group</span></div>

    <div class="person">
      <p class="person__name">Tomas Verbick</p>
      <p class="person__role">Project Manager</p>
      <p class="person__address">41 Barrow Crescent Hallam 5291</p>
    </div>

    <ul class="contacts">
      <li>
        <svg viewBox="0 0 12 12" aria-hidden="true"><path d="M1 4c0-2 2-3 5-3s5 1 5 3l-2 1-1-1.5H4L3 5 1 4zM3 6h6l1 5H2z"/></svg>
        (73) 0622 4783
      </li>
      <li>
        <svg viewBox="0 0 12 12" aria-hidden="true"><path d="M0 2h12v8H0z M1 3l5 4 5-4" stroke="#e9e9e9" stroke-width="1"/></svg>
        (03) 9418 6573
      </li>
      <li>
        <svg viewBox="0 0 12 12" aria-hidden="true"><circle cx="6" cy="6" r="5.5"/><path d="M.5 6h11M6 .5v11M3.5 2a7 7 0 0 0 0 8M8.5 2a7 7 0 0 1 0 8" stroke="#e9e9e9" stroke-width=".8" fill="none"/></svg>
        info@verbickgroup.com
      </li>
    </ul>

    <p class="tagline">Construction (Commercial &amp; Industrial) Civil Construction</p>
    <div class="card__band"><div class="card__band-grey"></div><div class="card__band-blue"></div></div>
  </section>

</div>
</body>
</html>
```